Create an awesome website for a medical clinic

This is a new website for a doctor's office. The site should be clean and modern, easy to navigate.

This is a wellness clinic, we want to help our clients have a healthy, active lifestyle. It should be friendly and inviting, and easy for them to call or schedule an appointment.

The site should be responsive and designed using the attached Bootstrap 3 PSD.

We will provide stock photos, until then please use stock photos from:

pixelharbor.com or
framequarry.com (preferred)

Some example sites of clean and modern designs that we like:

https://tulsaspinecare.com/
http://reachpastjoints.com/
http://turninghealthier.com/

Also attached is a temporary logo you can use.

Reason: Thank you everyone for your great designs - we need a little more time so I'm extending the project.

Need extra days to review

Also, the colors in the new logo I just linked to are the final colors of the logo, so feel free to use any complimentary colors to it.

Hi everyone, The boss wants to change the layout of the site a little bit - here's the revised layout: https://www.filecrate.com/s/k9rt31vx2qp84zn/notes%2011_29_2017.pdf?dl=0 And the graphic assets you can use are here: https://www.filecrate.com/s/k9rt31vx2qp84zn/notes%2011_29_2017.pdf?dl=0 Feel free to change the background color of the "topbar", and change the icons of the "why people trust us" if you want, these are just temporary placeholders. Thanks for your patience and hard work!

Target Market(s)

People seeking medical treatment (wellness clinic)

Industry/Entity Type

Doctor

Number of Pages Required

1 page

Font styles to use
Sans Serif

Colors
0592cd
33a6d7
abd037
9bcb3c

Requirements
Must have
• The home page should have: a strong hero image/slideshow, clinic phone number should be prominent and at the top of the page (in the nav), a "what to expect" section (this is like a FAQs section - see attachment), and a strong call to action (a button to call or schedule an appointment).
• The what to expect section is useful so that prospective clients can determine if we're a good fit for them or not. It's a basic, first-step pre-qualification block of information.
• Social media icons which links to our social media profiles should be included.
Nice to have
• - Link to 3 most recent blog entries
• - Testimonials
• - How a multilevel nav menu looks.

```html
<!DOCTYPE html>
<html lang="en">
<head>
<meta charset="utf-8">
<title>Wellness Clinic – About, Experts and Blog</title>
<link href="https://fonts.googleapis.com/css2?family=Open+Sans:wght@400;600&display=swap" rel="stylesheet">
<style>
  :root {
    --blue: #0592cd;
    --blue-light: #33a6d7;
    --green: #9bcb3c;
    --green-light: #abd037;
    --green-dark: #6f9a22;
    --text: #333333;
    --white: #ffffff;
  }
  * { box-sizing: border-box; margin: 0; padding: 0; }
  html, body { width: 1200px; height: 1200px; overflow: hidden; background: var(--white); }
  body { position: relative; font-family: "Open Sans", Arial, sans-serif; color: var(--text); }

  .section-title { position: absolute; font-weight: 400; font-size: 29px; line-height: 1; text-align: center; }

  /* About */
  .about-title { left: 168px; width: 392px; top: 25px; color: var(--blue); }
  .about-rule { position: absolute; left: 140px; top: 68px; width: 3px; height: 224px; background: var(--blue); }
  .about-text { position: absolute; left: 168px; top: 75px; width: 432px; font-size: 14px; line-height: 17.4px; }
  .about-text p + p { margin-top: 17px; }
  .about-photo { position: absolute; left: 612px; top: 11px; width: 448px; height: 299px;
    background: linear-gradient(120deg, #2f5f86 0%, #a9c7dc 45%, #e8eef3 70%, #c9dbe8 100%); }

  /* Experts */
  .experts-band { position: absolute; left: 75px; top: 346px; width: 1050px; height: 209px; background: var(--green); }
  .experts-title { left: 286px; width: 628px; top: 360px; color: var(--white); }
  .experts-rule { position: absolute; left: 286px; top: 399px; width: 628px; height: 2px; background: var(--white); }
  .expert-card { position: absolute; top: 439px; width: 212px; height: 361px; background: var(--white);
    box-shadow: 0 1px 5px rgba(0,0,0,0.18); }
  .expert-photo { position: absolute; left: 8px; top: 8px; width: 196px; height: 215px; }
  .expert-name { position: absolute; left: 26px; top: 229px; width: 190px; height: 28px; }
  .expert-name svg { position: absolute; left: 0; top: 0; }
  .expert-name span { position: relative; display: block; text-align: center; color: var(--white);
    font-weight: 600; font-size: 18px; line-height: 28px; padding-left: 6px; white-space: nowrap; }
  .expert-bio { position: absolute; left: 9px; top: 263px; width: 200px; font-size: 14px; line-height: 17.4px; }

  /* Blog */
  .blog-title { left: 286px; width: 628px; top: 832px; color: var(--blue); }
  .blog-rule { position: absolute; left: 286px; top: 871px; width: 628px; height: 2px; background: var(--blue); }
  .blog-card { position: absolute; top: 905px; width: 290px; height: 287px; }
  .blog-photo { position: absolute; left: 0; top: 0; width: 290px; height: 157px; }
  .blog-panel { position: absolute; left: 0; top: 157px; width: 290px; height: 130px; background: var(--blue); color: var(--white); }
  .blog-icon { position: absolute; left: 125px; top: -21px; }
  .blog-headline { position: absolute; left: 0; width: 290px; top: 22px; text-align: center; font-weight: 600; font-size: 19px; line-height: 24px; }
  .blog-excerpt { position: absolute; left: 14px; top: 47px; width: 270px; font-size: 14px; line-height: 17.4px; }
  .read-more { position: absolute; right: -4px; top: 106px; height: 20px; width: 98px; }
  .read-more svg { position: absolute; left: 0; top: 0; }
  .read-more span { position: relative; display: block; text-align: center; padding-left: 8px;
    font-weight: 600; font-size: 14px; line-height: 20px; color: var(--white); }
  .slider-arrow { position: absolute; top: 1028px; }
</style>
</head>
<body>

<section class="about">
  <h2 class="section-title about-title">About - Example Text</h2>
  <div class="about-rule"></div>
  <div class="about-text">
    <p>Tempus donec earum placerat, accumsan proin vitae, et tortor tincidunt sodales, libero duis aliquam lacus nisl nonummy, nulla elit molestie amet. Ad eos et, ipsum sodales purus urna sed. Suspendisse neque nulla neque lacus, sagittis massa, ullamcorper non. Sed felis pharetra donec lectus ipsum, sit diam elementum duis amet consectetuer, bibendum cras.</p>
    <p>Ut sit, wisi tortor porttitor sed pellentesque non in, ac montes lobortis pulvinar. Tempor consectetuer neque rhoncus a nulla ultrices, faucibus curabitur mauris<br>in rhoncus.</p>
  </div>
  <div class="about-photo" role="img" aria-label="Doctor in a white coat examining an X-ray, colleagues in the background"></div>
</section>

<section class="experts">
  <div class="experts-band"></div>
  <h2 class="section-title experts-title">Our Experts</h2>
  <div class="experts-rule"></div>

  <article class="expert-card" style="left:140px">
    <div class="expert-photo" role="img" aria-label="Smiling female doctor holding a clipboard in a clinic" style="background:linear-gradient(135deg,#dfe9ee,#c4d7e2 60%,#4d7fa8)"></div>
    <div class="expert-name"><svg width="190" height="28" viewBox="0 0 190 28"><polygon points="0,0 186,0 186,28 0,28 7,14" fill="#9bcb3c"/><polygon points="186,0 190,4 190,28 186,28" fill="#6f9a22"/></svg><span>Dr. Jane Smith</span></div>
    <p class="expert-bio">Lorem ipsum dolor sit amet, sagittis iure in magna libero nunc, maecenas quia diam at sed, enim dui, mauris ut dignissim cras enim egestas.</p>
  </article>

  <article class="expert-card" style="left:376px">
    <div class="expert-photo" role="img" aria-label="Therapist giving a leg massage to a patient" style="background:linear-gradient(135deg,#bdb6b2,#8c8480 50%,#e3d8d0)"></div>
    <div class="expert-name"><svg width="190" height="28" viewBox="0 0 190 28"><polygon points="0,0 186,0 186,28 0,28 7,14" fill="#9bcb3c"/><polygon points="186,0 190,4 190,28 186,28" fill="#6f9a22"/></svg><span>Dr. Jammes Smith</span></div>
    <p class="expert-bio">Lorem ipsum dolor sit amet, sagittis iure in magna libero nunc, maecenas quia diam at sed, enim dui, mauris ut dignissim cras enim egestas.</p>
  </article>

  <article class="expert-card" style="left:612px">
    <div class="expert-photo" role="img" aria-label="Male doctor with stethoscope seated at a desk" style="background:linear-gradient(135deg,#f2f2f2,#e0e2e4 60%,#c9b9a6)"></div>
    <div class="expert-name"><svg width="190" height="28" viewBox="0 0 190 28"><polygon points="0,0 186,0 186,28 0,28 7,14" fill="#9bcb3c"/><polygon points="186,0 190,4 190,28 186,28" fill="#6f9a22"/></svg><span>Dr. John Smith</span></div>
    <p class="expert-bio">Lorem ipsum dolor sit amet, sagittis iure in magna libero nunc, maecenas quia diam at sed, enim dui, mauris ut dignissim cras enim egestas.</p>
  </article>

  <article class="expert-card" style="left:848px">
    <div class="expert-photo" role="img" aria-label="Senior doctor reading a document in his office" style="background:linear-gradient(135deg,#a9b2b8,#dfe3e6 55%,#b79a72)"></div>
    <div class="expert-name"><svg width="190" height="28" viewBox="0 0 190 28"><polygon points="0,0 186,0 186,28 0,28 7,14" fill="#9bcb3c"/><polygon points="186,0 190,4 190,28 186,28" fill="#6f9a22"/></svg><span>Dr. Stephen Smith</span></div>
    <p class="expert-bio">Lorem ipsum dolor sit amet, sagittis iure in magna libero nunc, maecenas quia diam at sed, enim dui, mauris ut dignissim cras enim egestas.</p>
  </article>
</section>

<section class="blog">
  <h2 class="section-title blog-title">Blog Posts</h2>
  <div class="blog-rule"></div>

  <svg class="slider-arrow" style="left:95px" width="33" height="40" viewBox="0 0 33 40" aria-label="Previous"><rect width="33" height="40" rx="5" fill="#0592cd"/><polyline points="21,9 11,20 21,31" fill="none" stroke="#fff" stroke-width="2"/></svg>
  <svg class="slider-arrow" style="left:1072px" width="33" height="40" viewBox="0 0 33 40" aria-label="Next"><rect width="33" height="40" rx="5" fill="#0592cd"/><polyline points="12,9 22,20 12,31" fill="none" stroke="#fff" stroke-width="2"/></svg>

  <article class="blog-card" style="left:140px">
    <div class="blog-photo" role="img" aria-label="Pregnant women doing yoga on mats" style="background:linear-gradient(180deg,#f1ece4 0%,#e6d2b4 55%,#3a74c0 80%,#d9a35e 100%)"></div>
    <div class="blog-panel">
      <svg class="blog-icon" width="40" height="40" viewBox="0 0 40 40"><circle cx="20" cy="20" r="19" fill="#0592cd" stroke="#fff" stroke-width="2.5"/><rect x="14" y="11" width="12" height="16" rx="1" fill="none" stroke="#fff" stroke-width="1.5"/><path d="M17 15h6M17 18h6M17 21h6" stroke="#fff" stroke-width="1.3"/><path d="M12 14v15h11" fill="none" stroke="#fff" stroke-width="1.5"/></svg>
      <h3 class="blog-headline">Headline Example 1</h3>
      <p class="blog-excerpt">Lorem ipsum dolor sit amet, mus non convallis turpis a, sed sollicitudin quisquam wisi lectus proin ...</p>
      <div class="read-more"><svg width="98" height="20" viewBox="0 0 98 20"><polygon points="0,0 94,0 94,20 0,20 6,10" fill="#9bcb3c"/><polygon points="94,0 98,3 98,20 94,20" fill="#6f9a22"/></svg><span>Read more</span></div>
    </div>
  </article>

  <article class="blog-card" style="left:454px">
    <div class="blog-photo" role="img" aria-label="Doctor talking with a senior patient" style="background:linear-gradient(135deg,#e9e9e6,#cfd6dc 50%,#8fa7c2)"></div>
    <div class="blog-panel">
      <svg class="blog-icon" width="40" height="40" viewBox="0 0 40 40"><circle cx="20" cy="20" r="19" fill="#0592cd" stroke="#fff" stroke-width="2.5"/><rect x="14" y="11" width="12" height="16" rx="1" fill="none" stroke="#fff" stroke-width="1.5"/><path d="M17 15h6M17 18h6M17 21h6" stroke="#fff" stroke-width="1.3"/><path d="M12 14v15h11" fill="none" stroke="#fff" stroke-width="1.5"/></svg>
      <h3 class="blog-headline">Headline Example 2</h3>
      <p class="blog-excerpt">Lorem ipsum dolor sit amet, mus non convallis turpis a, sed sollicitudin quisquam wisi lectus proin ...</p>
      <div class="read-more"><svg width="98" height="20" viewBox="0 0 98 20"><polygon points="0,0 94,0 94,20 0,20 6,10" fill="#9bcb3c"/><polygon points="94,0 98,3 98,20 94,20" fill="#6f9a22"/></svg><span>Read more</span></div>
    </div>
  </article>

  <article class="blog-card" style="left:770px">
    <div class="blog-photo" role="img" aria-label="Woman exercising on a gym machine with a trainer" style="background:linear-gradient(100deg,#3b3a36,#8a7f6c 45%,#f4f1e4 75%,#cfc6b2)"></div>
    <div class="blog-panel">
      <svg class="blog-icon" width="40" height="40" viewBox="0 0 40 40"><circle cx="20" cy="20" r="19" fill="#0592cd" stroke="#fff" stroke-width="2.5"/><rect x="14" y="11" width="12" height="16" rx="1" fill="none" stroke="#fff" stroke-width="1.5"/><path d="M17 15h6M17 18h6M17 21h6" stroke="#fff" stroke-width="1.3"/><path d="M12 14v15h11" fill="none" stroke="#fff" stroke-width="1.5"/></svg>
      <h3 class="blog-headline">Headline Example 3</h3>
      <p class="blog-excerpt">Lorem ipsum dolor sit amet, mus non convallis turpis a, sed sollicitudin quisquam wisi lectus proin ...</p>
      <div class="read-more"><svg width="98" height="20" viewBox="0 0 98 20"><polygon points="0,0 94,0 94,20 0,20 6,10" fill="#9bcb3c"/><polygon points="94,0 98,3 98,20 94,20" fill="#6f9a22"/></svg><span>Read more</span></div>
    </div>
  </article>
</section>

</body>
</html>
```